Sable Grove products by Voldrin. Beauty, skin care cosmetic products

We are an all natural and organic beauty product company looking for a logo an label design ideas. Our motto is to make products that are safe, natural, in harmony with the earth and that really work. Our products will contribute to the transition from the Old Earth to the Sable Grove (as the image of the two worlds suggests). The earths can be mixed in the label. The label example is a rough sketch.
Updates

The label needs to be 1 (one) inch high and 7 inch long.

Need extra days to review

Target Market(s)

Products made with natural and organic ingredients. Beauty and skin products

Requirements
Must have
• My project must be standing out. We want customers to be draw to he product on the shelf. Wow, this label is different? what is it? All natural? I must try it.
• Must be bold but not outrageous.
• The two earth can be placed on right and left side of the tree of life on the second attachment
Nice to have
• The two Earth can be in the back ground suggesting that this product takes us from chemically and artificially filled products to something new that is in harmony with nature and health.
Should not have
• Should not be boring. Ordinary, easy to forget and ignore patterns, lettering, logos.

```html
<!DOCTYPE html>
<html lang="en">
<head>
<meta charset="utf-8">
<title>Voldrin Under-Arm-Balm Label</title>
<link rel="stylesheet" href="https://fonts.googleapis.com/css2?family=Open+Sans:wght@400;800&family=Sorts+Mill+Goudy&display=swap">
<style>
  :root {
    --stage: #3a3a3c;
    --label-blue: #1c5fb8;
    --label-deep: #0d1a4a;
    --earth-dark: #0b1326;
    --tree-green: #1f3b34;
    --accent-green: #7dc242;
    --headline: #ffffff;
    --text: #ffffff;
  }
  * { margin: 0; padding: 0; box-sizing: border-box; }
  html, body { width: 1200px; height: 857px; overflow: hidden; }
  body { background: var(--stage); position: relative; }

  .label {
    position: absolute; left: 40px; top: 348px;
    width: 1120px; height: 161px; overflow: hidden;
    background: linear-gradient(90deg, var(--label-blue) 0%, #1a4ea6 30%, var(--label-deep) 50%, #1a4aa8 70%, #2b5fc4 100%);
    border: 1px solid #2f7fd6;
    color: var(--text);
    font-family: "Sorts Mill Goudy", Georgia, serif;
  }
  .earth { position: absolute; border-radius: 50%; }
  .earth--old { left: 170px; top: -60px; width: 330px; height: 330px;
    background: radial-gradient(circle at 55% 50%, #1d3c57 0%, #0e1c30 60%, rgba(14,28,48,0) 72%); }
  .earth--new { left: 700px; top: -90px; width: 380px; height: 360px;
    background: radial-gradient(circle at 45% 45%, #3a6fd6 0%, #1e3f9a 50%, rgba(30,63,154,0) 72%); }
  .tree-of-life { position: absolute; left: 384px; top: -95px; width: 352px; height: 352px; border-radius: 50%;
    background: radial-gradient(circle, var(--earth-dark) 0%, #0f1d33 55%, var(--tree-green) 85%, #13233a 100%); }

  .panel-info { position: absolute; left: 24px; top: 18px; width: 340px; font-size: 10.4px; line-height: 13.3px; }
  .panel-info p { margin-bottom: 8px; }
  .panel-info strong { font-family: "Open Sans", Arial, sans-serif; font-weight: 800; font-size: 9.6px; letter-spacing: -0.2px; }
  .warning { border: 1px solid var(--text); padding: 4px 7px; width: 316px; margin-left: -7px; }

  .brand-block { position: absolute; left: 434px; top: 0; width: 252px; height: 161px; text-align: center; }
  .maker { position: absolute; top: 12px; width: 100%; font-size: 11px; }
  .arc { position: absolute; left: 0; top: 22px; }
  .brand-name { position: absolute; top: 52px; width: 100%; font-family: "Open Sans", Arial, sans-serif; font-weight: 800; font-size: 44px; line-height: 44px; color: var(--headline); letter-spacing: 0.5px; }
  .product-name { position: absolute; top: 97px; width: 100%; font-family: "Open Sans", Arial, sans-serif; font-weight: 800; font-size: 22px; line-height: 24px; color: var(--accent-green); }
  .free-from { position: absolute; top: 125px; width: 100%; font-family: "Open Sans", Arial, sans-serif; font-size: 12.5px; line-height: 13.5px; }
  .free-from b { font-weight: 800; }

  .panel-maker { position: absolute; left: 806px; top: 22px; font-size: 10.8px; line-height: 13.4px; }
  .best-before { position: absolute; left: 806px; top: 98px; width: 128px; height: 16px; background: #fff; color: #111; font-size: 10px; line-height: 16px; padding-left: 6px; }
  .net-weight { position: absolute; left: 808px; top: 125px; font-size: 10.8px; }
</style>
</head>
<body>
  <section class="label">
    <div class="earth earth--old" role="img" aria-label="Photo of the old Earth seen from space"></div>
    <div class="earth earth--new" role="img" aria-label="Photo of the new blue Earth seen from space"></div>
    <div class="tree-of-life" role="img" aria-label="Celtic tree of life ornament in a circle"></div>

    <div class="panel-info">
      <p><strong>INGREDIENTS:</strong> Organic Coconut (Cocos nucifera) Oil, Organic Bees Wax, Shea (Butyrospermum Parkii) Butter, Arrowroot (Mainhot Esculenta) Powder, Magnesium Oil, Nahcolite (Natural Baking Soda)</p>
      <p><strong>DIRECTIONS:</strong> With the finger or spatula apply a pee size product under the arm and spred it on, if applied night after a shave it might sting a bit. Wait a few minutes and the apply.</p>
      <p class="warning"><strong>WARNING:</strong> External use only. Discontinue use if irritation occurs. Do not apply to open cuts or wounds.</p>
    </div>

    <div class="brand-block">
      <p class="maker">Sable Grove Products by:</p>
      <svg class="arc" width="252" height="40" viewBox="0 0 252 40">
        <defs><path id="claim-arc" d="M14 36 Q126 2 238 36"/></defs>
        <text fill="#7dc242" font-family="Sorts Mill Goudy, Georgia, serif" font-size="14.5">
          <textPath href="#claim-arc" startOffset="50%" text-anchor="middle">100% NATURAL INGREDIENTS</textPath>
        </text>
        <line x1="80" y1="24" x2="172" y2="24" stroke="#ffffff" stroke-width="1.2"/>
      </svg>
      <h1 class="brand-name">VOLDRIN</h1>
      <h2 class="product-name">UNDER-ARM-BALM</h2>
      <p class="free-from"><b>No</b> Aluminum, <b>No</b> Parabens,<br><b>No</b> Phthalates</p>
    </div>

    <p class="panel-maker">Manufactured by Voldrin LLC<br>0000 Meadow Lane Road, Ash<br>ford MD 20000<br>Lear more at:<br>Voldrin.com</p>
    <div class="best-before">Best before:</div>
    <p class="net-weight">Net Wt. 2oz (56 g)</p>
  </section>
</body>
</html>
```